Risk Management Company in need of Business Card Design

We sell risk management insurance to Lenders (Banks, Credit Unions, Real Estate Trust).

We need a very clean, professional card that will leave a great impression.

We are looking to use a blue color for our logo on the card (Preferably close to royal blue but are open to looking at navy blue or any darker blues as well).

Please see the logo attached to get an idea. We are open to writing Harbor Ledger Under the logo or next to the logo. Really whatever looks best.

Target Market(s)

Banks, Credit Unions, Real Estate Trusts

Industry/Entity Type

Insurance

Contact Information for Business Card

Name: Tom Brandish
Title: Regional Sales Director
Email: tbrandish@harborledger-example.net
C:410-555-0137
D:410-555-0182
888-555-0149 Ext.205
F:443-555-0164 (We would like to see some cards without the fax number as well to compare)

Company Name: Harbor Ledger
Website: www.harborledger-example.net

Address: 718 E. Marlow St. Suite 340, Towson, MD 21287 (Preferably written on the bottom of the card in small print.)

Colors
0355a3
0455a3

Requirements
Nice to have
• We would like to see a couple of where the back has the logo in reverse colors (Logo White, Background Blue)

```html
<!DOCTYPE html>
<html lang="en">
<head>
<meta charset="utf-8">
<title>Harbor Ledger – Business Card</title>
<link href="https://fonts.googleapis.com/css2?family=Cinzel:wght@500;600&family=Open+Sans:wght@400;600;700&display=swap" rel="stylesheet">
<style>
  :root {
    --brand-blue: #0455a3;
    --brand-blue-deep: #034a8f;
    --silver-light: #f4f4f2;
    --silver-mid: #c9c9c6;
    --silver-dark: #9a9a97;
    --ink: #333333;
    --paper: #ffffff;
    --stage: #e9e9e7;
  }
  * { box-sizing: border-box; margin: 0; padding: 0; }
  html, body { width: 1200px; height: 786px; overflow: hidden; }
  body {
    background: var(--stage);
    position: relative;
    font-family: "Open Sans", Arial, sans-serif;
  }
  .card {
    position: absolute;
    width: 520px;
    height: 297px;
    overflow: hidden;
    box-shadow: 0 4px 14px rgba(0,0,0,0.18);
  }
  .card--front { left: 340px; top: 60px; }
  .card--back-blue { left: 60px; top: 430px; background: var(--brand-blue); }
  .card--back-white { left: 620px; top: 430px; background: var(--paper); }

  .front-bg { position: absolute; inset: 0; }

  .wordmark {
    font-family: "Cinzel", "Times New Roman", serif;
    font-weight: 600;
    letter-spacing: 0.5px;
    white-space: nowrap;
  }
  .front-wordmark {
    position: absolute;
    left: 40px;
    top: 110px;
    font-size: 24px;
    color: var(--paper);
  }
  .holder {
    position: absolute;
    right: 22px;
    top: 18px;
    text-align: right;
    color: var(--ink);
  }
  .holder__name { font-size: 16px; font-weight: 700; }
  .holder__title { font-size: 14px; margin-top: 2px; }

  .contacts {
    position: absolute;
    left: 40px;
    top: 163px;
    list-style: none;
    color: var(--paper);
    font-size: 12.5px;
    line-height: 22px;
  }
  .contacts li { display: flex; align-items: center; gap: 5px; white-space: nowrap; }
  .contacts small { font-size: 9px; margin-left: 3px; }
  .icon { width: 11px; height: 11px; flex: none; }
  .gap { display: inline-block; width: 6px; }

  .address {
    position: absolute;
    left: 312px;
    top: 168px;
    padding-left: 10px;
    border-left: 1px solid rgba(255,255,255,0.8);
    color: var(--paper);
    font-size: 12.5px;
    line-height: 18px;
    font-style: normal;
  }

  .back-content {
    position: absolute;
    inset: 0;
    display: flex;
    flex-direction: column;
    align-items: center;
    justify-content: center;
    gap: 16px;
  }
  .back-wordmark { font-size: 40px; }
  .card--back-blue .back-wordmark { color: var(--paper); }
  .card--back-white .back-wordmark { color: var(--brand-blue); }
  .back-web {
    font-size: 15px;
    font-weight: 700;
    letter-spacing: 2.5px;
  }
  .card--back-blue .back-web { color: var(--paper); }
  .card--back-white .back-web { color: #222; font-weight: 600; }
</style>
</head>
<body>

  <section class="card card--front" aria-label="Card front">
    <svg class="front-bg" viewBox="0 0 520 297" width="520" height="297" aria-hidden="true">
      <defs>
        <linearGradient id="silver" x1="0" y1="0" x2="1" y2="0">
          <stop offset="0" stop-color="var(--silver-mid)"/>
          <stop offset="0.45" stop-color="var(--silver-light)"/>
          <stop offset="1" stop-color="var(--silver-dark)"/>
        </linearGradient>
      </defs>
      <rect width="520" height="297" fill="url(#silver)"/>
      <path d="M0,74 C210,50 440,70 520,250" fill="none" stroke="var(--brand-blue)" stroke-width="3"/>
      <path d="M0,82 C214,60 436,82 514,297" fill="none" stroke="var(--silver-dark)" stroke-width="10"/>
      <path d="M0,88 C214,68 430,92 504,297 L0,297 Z" fill="var(--brand-blue)"/>
    </svg>

    <div class="holder">
      <p class="holder__name">Tom Brandish</p>
      <p class="holder__title">Regional Sales Director</p>
    </div>

    <p class="wordmark front-wordmark">Harbor Ledger</p>

    <ul class="contacts">
      <li>
        <svg class="icon" viewBox="0 0 12 12" aria-hidden="true"><rect x="3" y="0.5" width="6" height="11" rx="1" fill="none" stroke="#fff"/><rect x="4.3" y="2" width="3.4" height="5" fill="#fff"/></svg>
        410-555-0137
      </li>
      <li>
        <svg class="icon" viewBox="0 0 12 12" aria-hidden="true"><path d="M2,1 L4.5,1 L5,4 L3.6,5 C4.4,6.8 5.2,7.6 7,8.4 L8,7 L11,7.5 L11,10 C6,11 1,6 2,1 Z" fill="#fff"/></svg>
        888-555-0149<small>Ext.205</small>
      </li>
      <li>
        <svg class="icon" viewBox="0 0 12 12" aria-hidden="true"><rect x="1" y="5" width="10" height="6" rx="1" fill="#fff"/><rect x="3" y="1" width="6" height="4" fill="#fff"/></svg>
        443-555-0164<span class="gap"></span>
        <svg class="icon" viewBox="0 0 12 12" aria-hidden="true"><path d="M2,1 L4.5,1 L5,4 L3.6,5 C4.4,6.8 5.2,7.6 7,8.4 L8,7 L11,7.5 L11,10 C6,11 1,6 2,1 Z" fill="#fff"/></svg>
        410-555-0182
      </li>
      <li>
        <svg class="icon" viewBox="0 0 12 12" aria-hidden="true"><rect x="1" y="3" width="10" height="7" fill="#fff"/><path d="M1,3 L6,7 L11,3" fill="none" stroke="var(--brand-blue)"/></svg>
        tbrandish@harborledger-example.net
      </li>
      <li>
        <svg class="icon" viewBox="0 0 12 12" aria-hidden="true"><circle cx="6" cy="6" r="5" fill="none" stroke="#fff"/><path d="M1,6 H11 M6,1 C3,4 3,8 6,11 M6,1 C9,4 9,8 6,11" fill="none" stroke="#fff" stroke-width="0.8"/></svg>
        www.harborledger-example.net
      </li>
    </ul>

    <address class="address">
      718 E. Marlow St.<br>
      Suite 340, Towson<br>
      MD 21287
    </address>
  </section>

  <section class="card card--back-blue" aria-label="Card back, blue">
    <div class="back-content">
      <p class="wordmark back-wordmark">Harbor Ledger</p>
      <p class="back-web">www.harborledger-example.net</p>
    </div>
  </section>

  <section class="card card--back-white" aria-label="Card back, white">
    <div class="back-content">
      <p class="wordmark back-wordmark">Harbor Ledger</p>
      <p class="back-web">www.harborledger-example.net</p>
    </div>
  </section>

</body>
</html>
```